WordPress design (BRKT)

We need a wordpress design for an established auction and real estate company based in Viginia- "Bid Bold.... Move Swiftly!". The winning design will incorporate a professional color scheme with company logo in a clean layout.
Industry/Entity Type
Real Estate
Requirements
Must have
- Navigation:
- 1) Home
- 2) Services
- 3) Auctions
- 4) Gala Benefit
- 5) Appraisals
- 6) Past Successes
- 7) About BRKT
- 8) Contact us
- Colors will be those in the attached logo. design should be able to be developed in responsive theme. Wants a "very clean and professional and sharp" design. Site will have slideshow that is relatively small, not a large portion of the design. Please use stock real estate image.
- Footer will have attached logos and contact info for the client.
Nice to have
- A representative drop down menu will be nice to see.

```html
<!DOCTYPE html>
<html lang="en">
<head>
<meta charset="utf-8">
<title>BRKT – Auctions &amp; Real Estate</title>
<link rel="stylesheet" href="https://fonts.googleapis.com/css2?family=Tinos:wght@400;700&family=Arimo:wght@400;700&display=swap">
<style>
:root{
  --ink:#241f1f;
  --gold:#b08a4a;
  --gold-light:#e2b466;
  --gold-box-top:#c49d5f;
  --gold-box-bottom:#a67b3d;
  --red:#a8140f;
  --text:#222;
  --rule:#d6d6d6;
  --paper:#fff;
}
*{box-sizing:border-box;margin:0;padding:0}
html,body{width:816px;height:1200px;overflow:hidden;background:var(--paper)}
body{position:relative;font-family:"Arimo",Arial,sans-serif;color:var(--text)}
.abs{position:absolute}

/* header */
.masthead{left:0;top:35px;width:816px;height:363px;background:var(--ink);border-top:2px solid var(--gold)}
.brand{left:92px;top:18px;width:104px;text-align:center;color:#fff;font-family:"Tinos",serif}
.brand-mark{display:block;margin:0 auto 2px;width:14px;height:14px;background:var(--gold)}
.brand-name{font-size:20px;letter-spacing:1px;line-height:20px}
.brand-tag{font-size:5px;letter-spacing:.4px;color:#ddd;margin-top:1px}
.main-nav{left:262px;top:42px;width:484px;height:14px;display:flex;justify-content:space-between;z-index:2}
.main-nav a{white-space:nowrap;color:#fff;font-size:9.5px;text-decoration:none}
.main-nav a.is-active{color:var(--gold-light)}
.hero{left:69px;top:84px;width:677px;height:306px;background:linear-gradient(180deg,#9fb8da 0%,#c5cfd8 35%,#8d8376 65%,#4b4338 100%)}
.dropdown{left:344px;top:66px;width:93px;height:62px;background:var(--gold);padding:5px 0 0 4px;z-index:3}
.dropdown::before{content:"";position:absolute;left:30px;top:-6px;border:6px solid transparent;border-top:0;border-bottom-color:var(--gold)}
.dropdown a{display:block;color:#fff;font-size:9px;line-height:19px;text-decoration:none}

/* welcome */
.welcome{left:70px;top:420px;width:452px}
.welcome h1{font-family:"Tinos",serif;font-weight:400;font-size:20px;color:var(--ink);margin-bottom:6px}
.welcome h1 span{color:var(--gold);font-weight:700;letter-spacing:.5px}
.welcome p{font-size:9px;line-height:12.4px;margin-bottom:12px}

.signup{left:547px;top:423px;width:199px;height:101px;background:linear-gradient(180deg,var(--gold-box-top),var(--gold-box-bottom));padding:7px 12px;color:#fff}
.signup h2{font-family:"Tinos",serif;font-size:16px;font-weight:700;margin-bottom:5px}
.signup p{font-size:8px;line-height:10.5px;width:155px}
.signup-form{position:absolute;left:10px;top:62px;width:178px;height:23px;display:flex}
.signup-form span{flex:1;background:#fff;font-size:8px;color:#999;padding:7px 7px}
.signup-form b{width:30px;background:#1f1b1b;color:#fff;font-size:10px;text-align:center;line-height:23px}

/* listings */
.listing{left:69px;width:468px;height:213px;border:1px solid var(--rule);background:#fafafa}
.listing-title{position:absolute;left:3px;top:4px;width:462px;height:28px;background:#000;color:#fff;font-family:"Tinos",serif;font-weight:700;font-size:12.6px;letter-spacing:.3px;padding:6px 7px}
.thumb-card{position:absolute;left:7px;top:45px;width:107px;height:115px;border:1px solid var(--rule);background:#fff}
.thumb{position:absolute;left:6px;top:7px;width:92px;height:63px;border:1px solid #777;background:linear-gradient(180deg,#9bb1cf 0%,#d4a07a 50%,#3b4663 100%)}
.details-btn{position:absolute;left:6px;top:82px;width:92px;height:22px;background:#222;color:#fff;font-size:11px;line-height:22px;padding-left:33px}
.details-btn svg{position:absolute;left:11px;top:4px}
.info-card{position:absolute;left:118px;width:339px;border:1px solid var(--rule);background:#fff;padding:5px 5px;font-size:9px;line-height:12.2px}
.info-card.lead{top:45px;height:74px}
.info-card.onsite{top:128px;height:75px}
.info-card h3{font-size:10px;font-weight:700;color:#111;line-height:12px;margin-bottom:4px;text-align:justify;letter-spacing:.4px}
.info-card h4{font-size:9.6px;font-weight:700;color:var(--red);margin-bottom:3px}
.info-card p{text-align:justify}

/* sidebar */
.side-panel{left:546px;width:201px;border:1px solid var(--rule);background:#fff}
.side-head{margin:2px;height:25px;background:#000;color:#fff;font-family:"Tinos",serif;font-weight:700;font-size:11.5px;letter-spacing:.6px;text-align:center;line-height:25px}
.featured{top:548px;height:162px}
.featured h5{color:#9a7335;font-size:10px;text-align:center;margin-top:8px}
.featured-photo{margin:6px auto 0;width:153px;height:67px;border:1px solid #777;background:linear-gradient(180deg,#a8bad3 0%,#d6a27b 45%,#36415d 100%)}
.featured p{font-size:8.6px;line-height:10.4px;text-align:center;margin-top:3px}
.testimonials{top:723px;height:144px}
.quote{padding:9px 8px 0 12px;font-size:9px;line-height:13.6px}
.quote i{font-family:"Tinos",serif;font-size:14px;font-style:normal;font-weight:700;color:#444}
.quote-author{font-weight:700;font-style:italic;color:var(--red);font-size:8.6px;text-align:right;padding-right:6px;margin-top:-4px}
.videos{top:873px;height:153px}
.video{position:relative;margin:0 2px;height:122px;background:linear-gradient(180deg,#c7d3e2 0%,#d6d6d2 40%,#8c8e86 75%,#5a6a46 100%)}
.video-controls{position:absolute;left:0;bottom:0;width:100%;height:14px;background:#eee;border-top:1px solid #ccc;font-size:6.5px;color:#222}

/* footer */
.site-footer{left:0;top:1058px;width:816px;height:142px;background:var(--ink)}
.social{position:absolute;top:20px;width:31px;height:31px;border-radius:6px;background:#4b4545}
.footer-links{position:absolute;left:71px;top:78px;color:#fff;font-size:8.2px;word-spacing:1px}
.footer-contact{position:absolute;left:71px;top:95px;color:#fff;font-size:8.2px}
.footer-copy{position:absolute;left:71px;top:114px;color:#fff;font-size:8.2px}
.badge{position:absolute;background:#6b6464;border-radius:2px}
</style>
</head>
<body>

<header class="abs masthead"></header>
<div class="abs brand">
  <span class="brand-mark"></span>
  <div class="brand-name">BRKT</div>
  <div class="brand-tag">AUCTIONS · APPRAISALS · CONSULTING</div>
</div>
<nav class="abs main-nav">
  <a>Home</a>
  <a>Services</a>
  <a class="is-active">Auctions</a>
  <a>Gala Benefit</a>
  <a>Appraisals</a>
  <a>Past Successes</a>
  <a>About BRKT</a>
  <a>Contact us</a>
</nav>
<div class="abs hero" role="img" aria-label="Two-storey suburban house at dusk with an auction sign on the lawn"></div>
<div class="abs dropdown">
  <a>#1 Online Auctions</a>
  <a>#2 Online Auctions</a>
  <a>#3 Online Auctions</a>
</div>

<section class="abs welcome">
  <h1>Welcome to <span>BRKT</span></h1>
  <p>simply dummy text of the printing and typesetting industry. Lorem Ipsum has been the industry's standard dummy text ever since the 1500s, when an unknown printer took a galley of type and scrambled it to make a type specimen book. remaining essentially unchanged. It was popularised in the 1960s with the release of</p>
  <p>Transfer sheets containing Lorem Ipsum passages, and more recently with desktop publishing software like Layout Studio including versions of Lorem Ipsum</p>
</section>

<aside class="abs signup">
  <h2>Email Sign-Up</h2>
  <p>Subscribe to Upcoming Auctions and our Free E-mail Newsletter.</p>
  <div class="signup-form"><span>Enter Your Email Address...</span><b>Go</b></div>
</aside>

<article class="abs listing" style="top:547px">
  <div class="listing-title">BRKT Real estate simply of the printing and typesetting</div>
  <div class="thumb-card">
    <div class="thumb" role="img" aria-label="Crowd gathered in front of a tiled-roof house at an auction"></div>
    <div class="details-btn"><svg width="14" height="14" viewBox="0 0 14 14"><circle cx="5.5" cy="5.5" r="4" fill="none" stroke="#ddd" stroke-width="1.6"/><line x1="8.5" y1="8.5" x2="13" y2="13" stroke="#ddd" stroke-width="2"/></svg>Details</div>
  </div>
  <div class="info-card lead">
    <h3>ONLINE NOW Internet Only Bidding Starts Closing Monday August 12th at 1:37PM</h3>
    <p>This former coffee cafe has closed and all items have been relocated to a sterling va warehouse for easy pick up. refrigerated equipment, counter top pizza ovens, chairs, stools, and more. ONLINE NOW!!! M1806</p>
  </div>
  <div class="info-card onsite">
    <h4>Live On-Site Auction</h4>
    <p>Began:&nbsp; Friday, May 24, 2013 at 10:06 AM EDT<br>Location<br>218 Meadow Ct. NW<br>Linton, IA 50412</p>
  </div>
</article>

<article class="abs listing" style="top:777px">
  <div class="listing-title">BRKT Real estate simply of the printing and typesetting</div>
  <div class="thumb-card">
    <div class="thumb" role="img" aria-label="Crowd gathered in front of a tiled-roof house at an auction"></div>
    <div class="details-btn"><svg width="14" height="14" viewBox="0 0 14 14"><circle cx="5.5" cy="5.5" r="4" fill="none" stroke="#ddd" stroke-width="1.6"/><line x1="8.5" y1="8.5" x2="13" y2="13" stroke="#ddd" stroke-width="2"/></svg>Details</div>
  </div>
  <div class="info-card lead">
    <h3>ONLINE NOW Internet Only Bidding Starts Closing Monday August 12th at 1:37PM</h3>
    <p>This former coffee cafe has closed and all items have been relocated to a sterling va warehouse for easy pick up. refrigerated equipment, counter top pizza ovens, chairs, stools, and more. ONLINE NOW!!! M1806</p>
  </div>
  <div class="info-card onsite">
    <h4>Live On-Site Auction</h4>
    <p>Began:&nbsp; Friday, May 24, 2013 at 10:06 AM EDT<br>Location<br>218 Meadow Ct. NW<br>Linton, IA 50412</p>
  </div>
</article>

<aside class="abs side-panel featured">
  <div class="side-head">FEATURED AUCTION</div>
  <h5>Industrial auction &amp; appraisal</h5>
  <div class="featured-photo" role="img" aria-label="Auction crowd in front of a house"></div>
  <p>07/10/13 at 12:00 PM EDT<br>P.O. Box 41172<br>Millbrook, VA 24061</p>
</aside>

<aside class="abs side-panel testimonials">
  <div class="side-head">CLIENT TESTIMONIALS</div>
  <div class="quote"><i>“</i> Contrary to popular belief, Lorem Ipsum is not simply random text. It has roots in a piece of classical Latin literature from 45 BC, making it over 2000 years old. Edwin Harrow, a Latin professor at Ashford College. <i>”</i></div>
  <div class="quote-author">By Daniel Forsythe</div>
</aside>

<aside class="abs side-panel videos">
  <div class="side-head">OUR VIDEOS</div>
  <div class="video" role="img" aria-label="Video still of a grey clapboard house with a front porch">
    <svg class="abs" style="left:73px;top:30px" width="38" height="38" viewBox="0 0 38 38"><circle cx="19" cy="19" r="18" fill="#111" stroke="#fff" stroke-width="1.5"/><polygon points="14,10 28,19 14,28" fill="#fff"/></svg>
    <div class="video-controls">
      <svg class="abs" style="left:5px;top:3px" width="7" height="7" viewBox="0 0 7 7"><polygon points="0,0 7,3.5 0,7" fill="#111"/></svg>
      <span class="abs" style="left:20px;top:3px">00:00</span>
      <span class="abs" style="left:46px;top:5px;width:70px;height:3px;background:#bbb"></span>
      <span class="abs" style="left:122px;top:3px">00:00</span>
      <span class="abs" style="left:156px;top:4px;width:22px;height:5px;background:repeating-linear-gradient(90deg,#333 0 1px,transparent 1px 3px)"></span>
      <svg class="abs" style="left:184px;top:3px" width="8" height="8" viewBox="0 0 8 8"><path d="M0 3V0h3M5 0h3v3M8 5v3H5M3 8H0V5" fill="none" stroke="#333"/></svg>
    </div>
  </div>
</aside>

<footer class="abs site-footer">
  <span class="social" style="left:78px"></span>
  <span class="social" style="left:122px"></span>
  <span class="social" style="left:167px"></span>
  <span class="social" style="left:214px"></span>
  <div class="footer-links">Home &nbsp;| &nbsp;Auctions &nbsp;| &nbsp;Buyers &nbsp;| &nbsp;Sellers &nbsp;| &nbsp;About Us &nbsp;| &nbsp;News &amp; Events &nbsp;| &nbsp;Contact Us</div>
  <div class="footer-contact">Phone: 555- 014-2290, Email: info@brktauctions.example</div>
  <div class="footer-copy">Copyright © 2013 Harlow Auctioneers. All rights reserved.</div>

  <span class="badge" style="left:478px;top:10px;width:26px;height:28px"></span>
  <span class="badge" style="left:517px;top:14px;width:58px;height:20px"></span>
  <span class="badge" style="left:588px;top:12px;width:30px;height:26px"></span>
  <span class="badge" style="left:631px;top:14px;width:56px;height:21px"></span>
  <span class="badge" style="left:707px;top:13px;width:39px;height:22px"></span>
  <span class="badge" style="left:476px;top:62px;width:55px;height:14px"></span>
  <span class="badge" style="left:548px;top:56px;width:34px;height:32px"></span>
  <span class="badge" style="left:601px;top:58px;width:60px;height:30px"></span>
  <span class="badge" style="left:682px;top:57px;width:64px;height:30px"></span>
  <span class="badge" style="left:588px;top:105px;width:34px;height:26px"></span>
  <span class="badge" style="left:632px;top:102px;width:32px;height:32px"></span>
  <span class="badge" style="left:686px;top:102px;width:55px;height:30px"></span>
</footer>

</body>
</html>
```